I need a website designed. I am a mortgage loan officer and would like to have a website for me and my team where i can post resources, videos and blog information for my clients. A website like themorvaskteam.com .

The theme is - The Pelkins Team - Home Loan Group powered by Brightwell Home Loans -

Target Market(s)

B2B (Real Estate Agents)and B2C (Home buyers and refinancing)

Industry/Entity Type

Mortgage Lender

Coding

Coded - Design and coding required

Number of Pages Required

5+ page

Font styles to use
Serif
Sans Serif

Colors

Designer to choose colors to be used in the design.

Requirements
Must have
• Disclaimers: Licensed by the Bureau of Lending Affairs under the Pacific Credit Providers Act. Loans made or arranged pursuant to a Pacific Credit Providers Act License. Equal Housing Lender Brightwell Cannot Accept mortgage applications for properties located in New York via this site
• Mobile Friendly
Nice to have
• Main Links: Home, About Us(see team flyer), Mortgage 101, Contact Us (formzig form)

```html
<!DOCTYPE html>
<html lang="en">
<head>
<meta charset="utf-8">
<title>The Pelkins Team – Home Loan Group</title>
<link href="https://fonts.googleapis.com/css2?family=Barlow:wght@400;500;600;700&display=swap" rel="stylesheet">
<style>
:root{
  --blue:#2b78c6;
  --blue-dark:#1f63ad;
  --ink:#1d2633;
  --text:#4a4f57;
  --muted:#8a9099;
  --line:#c9ccd1;
  --gray-bg:#eceef1;
  --footer:#1f2631;
  --footer-text:#b9bec6;
  --white:#ffffff;
}
*{margin:0;padding:0;box-sizing:border-box}
html,body{width:1200px;height:3488px;overflow:hidden}
body{position:relative;font-family:"Barlow",Arial,sans-serif;color:var(--text);background:var(--white)}
.abs{position:absolute}

/* header */
.topbar{left:0;top:0;width:1200px;height:51px;background:var(--blue)}
.search{left:70px;top:11px;width:197px;height:29px;border-radius:15px;background:var(--white);font-size:12px;font-weight:700;color:var(--ink);padding:7px 16px;letter-spacing:.5px}
.search svg{position:absolute;right:12px;top:7px}
.contact-info{right:48px;top:15px;color:var(--white);font-size:12px;font-weight:600;display:flex;gap:26px;align-items:center}
.contact-info span{display:flex;gap:6px;align-items:center}
.navbar{left:0;top:51px;width:1200px;height:70px;background:var(--white)}
.brand-box{left:485px;top:0;width:230px;height:121px;background:var(--white);display:flex;align-items:center;justify-content:center;gap:10px}
.brand-name{font-size:25px;font-weight:700;color:var(--blue);letter-spacing:.5px;white-space:nowrap}
.brand-dot{width:12px;height:12px;background:var(--blue)}
.nav-link{top:76px;font-size:14px;font-weight:700;color:var(--ink);letter-spacing:.4px}
.nav-link.active{color:var(--blue)}

/* hero */
.hero{left:0;top:121px;width:1200px;height:500px;background:linear-gradient(120deg,#e9e6e1 0%,#cfc6bb 35%,#8e8a86 55%,#d9d4ce 80%,#f1efec 100%)}
.hero-title{left:0;top:268px;width:1200px;text-align:center;color:var(--white);text-shadow:0 3px 10px rgba(0,0,0,.35)}
.hero-title .l1{display:block;font-size:100px;font-weight:700;line-height:100px;letter-spacing:1px}
.hero-title .l2{display:block;font-size:60px;font-weight:600;line-height:66px;letter-spacing:1px}
.btn-solid{left:498px;top:453px;width:204px;height:47px;background:#6b6e72;color:var(--white);font-size:13px;font-weight:700;letter-spacing:.6px;display:flex;align-items:center;justify-content:center}
.dots{left:560px;top:580px;display:flex;gap:10px}
.dots i{display:block;width:8px;height:8px;border-radius:50%;background:rgba(255,255,255,.6)}
.dots i.on{background:var(--white)}

/* about */
.about{left:0;top:621px;width:1200px;height:444px;background:linear-gradient(180deg,var(--blue) 0%,var(--blue-dark) 100%)}
.section-title{left:0;width:1200px;text-align:center;font-size:30px;font-weight:700;letter-spacing:1px}
.about .section-title{top:78px;color:var(--white)}
.about-text{left:300px;top:172px;width:600px;text-align:center;color:#e3edf8;font-size:12.5px;line-height:19px}
.about-text p+p{margin-top:14px}
.btn-outline{width:204px;height:53px;border:1.5px solid currentColor;font-size:13px;font-weight:700;letter-spacing:.6px;display:flex;align-items:center;justify-content:center}
.about .btn-outline{left:498px;top:319px;color:var(--white)}
.about-corner{left:0;top:0}

/* videos */
.videos-title{top:1152px;color:var(--blue)}
.video{width:338px}
.video-thumb{width:338px;height:239px;position:relative;box-shadow:0 2px 6px rgba(0,0,0,.15)}
.video-thumb svg{position:absolute;left:139px;top:89px}
.video-caption{margin-top:24px;text-align:center;font-size:14px;font-weight:700;color:var(--ink);letter-spacing:.3px}

/* team */
.team{left:0;top:1635px;width:1200px;height:731px;background:var(--gray-bg)}
.team .section-title{top:88px;color:var(--blue)}
.member{width:520px;height:175px}
.member-photo{position:absolute;left:0;top:0;width:189px;height:174px;background:linear-gradient(160deg,#d7d9dc,#8b8f95)}
.member-info{position:absolute;left:205px;top:6px;width:300px}
.member-name{font-size:19px;font-weight:700;color:var(--ink);letter-spacing:.3px}
.member-role{font-size:11.5px;font-weight:600;color:var(--ink);margin-top:2px}
.member-rule{width:48px;height:1px;background:var(--line);margin:9px 0 8px}
.member-meta{font-size:10.5px;line-height:15px;color:var(--muted)}
.btn-small{position:absolute;left:205px;top:144px;width:107px;height:30px;border:1.5px solid var(--blue);color:var(--blue);background:var(--white);font-size:11px;font-weight:700;display:flex;align-items:center;justify-content:center}

/* blog */
.blog-title{top:2415px;color:var(--blue)}
.post{width:338px}
.post-image{width:338px;height:242px;box-shadow:0 2px 6px rgba(0,0,0,.15)}
.post-title{margin-top:31px;font-size:13px;font-weight:700;line-height:17px;color:var(--ink)}
.post-body{margin-top:9px;font-size:11px;line-height:15px;color:var(--muted)}
.post-rule{width:60px;height:1px;background:var(--line);margin:22px 0 16px}
.post-date{font-size:13px;font-weight:700;color:var(--blue)}
.blog-more{left:498px;top:3007px;color:var(--ink);border-color:var(--blue)}

/* footer */
.footer{left:0;top:3105px;width:1200px;height:383px;background:var(--footer)}
.footer-brand{left:70px;top:76px;display:flex;align-items:center;gap:8px}
.footer-brand .brand-name{font-size:22px}
.footer-partners{left:100px;top:152px;display:flex;align-items:center;gap:14px}
.badge{width:34px;height:38px;background:var(--white)}
.partner-name{font-size:14px;font-weight:600;color:#6f8fb6;letter-spacing:.3px}
.fcol-title{font-size:12px;font-weight:700;color:var(--blue);letter-spacing:.6px}
.fcol ul{list-style:none;margin-top:16px}
.fcol li{font-size:11.5px;font-weight:600;color:var(--white);line-height:20px;letter-spacing:.3px}
.res-item{display:flex;gap:8px;margin-top:14px;width:300px}
.res-item .arrow{color:var(--muted);font-size:11px}
.res-text{font-size:10.5px;line-height:14px;color:#6f7681}
.res-date{font-size:11px;font-weight:700;color:var(--blue);margin-top:4px}
.res-nav{left:1075px;top:42px;color:var(--white);font-size:14px;letter-spacing:8px}
.disclaimer-title{left:0;top:258px;width:1200px;text-align:center;font-size:12px;font-weight:700;color:var(--blue)}
.disclaimer{left:80px;top:284px;width:1040px;text-align:center;font-size:12px;line-height:18px;color:var(--footer-text)}
.footer-bottom{left:0;top:348px;width:1200px;text-align:center;font-size:11px;font-weight:600;color:var(--footer-text);letter-spacing:.4px}
.footer-rule{left:0;top:333px;width:1200px;height:1px;background:#2d3541}
</style>
</head>
<body>

<header>
  <div class="abs topbar"></div>
  <div class="abs search">SEARCH
    <svg width="14" height="14" viewBox="0 0 14 14"><circle cx="6" cy="6" r="4.5" fill="none" stroke="#1d2633" stroke-width="1.8"/><line x1="9.3" y1="9.3" x2="13" y2="13" stroke="#1d2633" stroke-width="1.8"/></svg>
  </div>
  <div class="abs contact-info">
    <span><svg width="9" height="12" viewBox="0 0 9 12"><path d="M4.5 0A4.5 4.5 0 0 0 0 4.5C0 8 4.5 12 4.5 12S9 8 9 4.5A4.5 4.5 0 0 0 4.5 0z" fill="#fff"/><circle cx="4.5" cy="4.5" r="1.6" fill="#2b78c6"/></svg>2260 LAKEVIEW RD, SUITE 104, ORLANDO FL 32801</span>
    <span><svg width="11" height="11" viewBox="0 0 11 11"><path d="M2.2 0.5l2 2.3-1.1 1.5a7 7 0 0 0 3.6 3.6l1.5-1.1 2.3 2-1.2 1.7C4.9 10.3.7 6.1 0.5 1.7z" fill="#fff"/></svg>1-407-555-0148</span>
  </div>
  <div class="abs navbar"></div>
  <div class="abs brand-box"><span class="brand-dot"></span><span class="brand-name">THE PELKINS TEAM</span></div>
  <nav>
    <span class="abs nav-link active" style="left:244px">HOME</span>
    <span class="abs nav-link" style="left:333px">ABOUT US</span>
    <span class="abs nav-link" style="left:726px">MORTGAGE 101</span>
    <span class="abs nav-link" style="left:875px">CONTACT US</span>
  </nav>
</header>

<section>
  <div class="abs hero" role="img" aria-label="Photo of a young couple reviewing home loan papers together on a sofa"></div>
  <h1 class="abs hero-title"><span class="l1">THE PELKINS TEAM</span><span class="l2">HOME LOAN GROUP</span></h1>
  <div class="abs btn-solid">LEARN MORE</div>
  <div class="abs dots"><i class="on"></i><i></i><i></i><i></i></div>
</section>

<section class="abs about">
  <svg class="abs about-corner" width="1200" height="444" viewBox="0 0 1200 444">
    <polygon points="790,444 965,240 1200,400 1200,444" fill="#ffffff"/>
  </svg>
  <h2 class="abs section-title">ABOUT US</h2>
  <div class="abs about-text">
    <p>Qui dolorem ipsum quia dolor sit amet, consectetur, adipisci velit, sed quia non numquam eius modi tempora incidunt ut labore et dolore magnam aliquam quaerat voluptatem.</p>
    <p>Ut enim ad minima veniam, quis nostrum exercitationem ullam corporis suscipit laboriosam, nisi ut aliquid ex ea commodi qui dolorem ipsum quia dolor sit amet, consectetur, adipisci velit, sed quia non numquam eius modi tempora.</p>
  </div>
  <div class="abs btn-outline">READ MORE</div>
</section>

<section>
  <h2 class="abs section-title videos-title">VIDEOS</h2>
  <div class="abs video" style="left:67px;top:1275px">
    <div class="video-thumb" role="img" aria-label="Video still of a family touring a bright home interior with an agent" style="background:linear-gradient(135deg,#f1efec,#cdbfae 60%,#9a8f84)">
      <svg width="60" height="60" viewBox="0 0 60 60"><circle cx="30" cy="30" r="27" fill="#2b78c6" stroke="#fff" stroke-width="3"/><polygon points="24,18 24,42 43,30" fill="#fff"/></svg>
    </div>
    <div class="video-caption">QUIA DOLOR SIT AMET, CONSECTETU</div>
  </div>
  <div class="abs video" style="left:433px;top:1275px">
    <div class="video-thumb" role="img" aria-label="Video still of a house with a lit wooden deck at dusk" style="background:linear-gradient(180deg,#3c4a5a,#6b5645 55%,#a0714a)">
      <svg width="60" height="60" viewBox="0 0 60 60"><circle cx="30" cy="30" r="27" fill="#2b78c6" stroke="#fff" stroke-width="3"/><polygon points="24,18 24,42 43,30" fill="#fff"/></svg>
    </div>
    <div class="video-caption">OCCAECATI CUPIDITATE NON PROVIDENT</div>
  </div>
  <div class="abs video" style="left:796px;top:1275px">
    <div class="video-thumb" role="img" aria-label="Video still of a family relaxing on the porch of their new home" style="background:linear-gradient(160deg,#c9d2c0,#8c8a7a 55%,#d8d4cb)">
      <svg width="60" height="60" viewBox="0 0 60 60"><circle cx="30" cy="30" r="27" fill="#2b78c6" stroke="#fff" stroke-width="3"/><polygon points="24,18 24,42 43,30" fill="#fff"/></svg>
    </div>
    <div class="video-caption">POSSIMUS, OMNIS VOLUPTAS ASSUMENDA</div>
  </div>
</section>

<section class="abs team">
  <h2 class="abs section-title">OUR TEAM</h2>
  <article class="abs member" style="left:67px;top:205px">
    <div class="member-photo" role="img" aria-label="Portrait of Marco Pelkins"></div>
    <div class="member-info">
      <div class="member-name">MARCO PELKINS</div>
      <div class="member-role">Producing Branch Manager</div>
      <div class="member-rule"></div>
      <div class="member-meta">Brightwell Home Loans, Inc – NMLS 48217<br>marco.pelkins@brightwellloans.com<br>Office: (407) 555-0171<br>Fax: (855) 555-0123</div>
    </div>
    <div class="btn-small">VIEW MORE</div>
  </article>
  <article class="abs member" style="left:612px;top:205px">
    <div class="member-photo" role="img" aria-label="Portrait of Tomas Reyvel"></div>
    <div class="member-info">
      <div class="member-name">TOMAS REYVEL</div>
      <div class="member-role">Loan Partner</div>
      <div class="member-rule"></div>
      <div class="member-meta">Brightwell Home Loans, Inc – NMLS 48217<br>NMLS ID 2093318<br>tomas.reyvel@brightwellloans.com<br>(407) 555-0148</div>
    </div>
    <div class="btn-small">VIEW MORE</div>
  </article>
  <article class="abs member" style="left:67px;top:431px">
    <div class="member-photo" role="img" aria-label="Portrait of Luis Dantera"></div>
    <div class="member-info">
      <div class="member-name">LUIS DANTERA</div>
      <div class="member-role">Loan Processor</div>
      <div class="member-rule"></div>
      <div class="member-meta">NMLS ID 2175640<br>luis.dantera@brightwellloans.com<br>(407) 555-0196</div>
    </div>
    <div class="btn-small">VIEW MORE</div>
  </article>
  <article class="abs member" style="left:612px;top:431px">
    <div class="member-photo" role="img" aria-label="Portrait of Greta Holloway"></div>
    <div class="member-info">
      <div class="member-name">GRETA HOLLOWAY</div>
      <div class="member-role">Closing Coordinator/Team Leader</div>
      <div class="member-rule"></div>
      <div class="member-meta">NMLS 2238905<br>greta.holloway@brightwellloans.com<br>(407) 555-0112</div>
    </div>
    <div class="btn-small">VIEW MORE</div>
  </article>
</section>

<section>
  <h2 class="abs section-title blog-title">BLOG</h2>
  <article class="abs post" style="left:67px;top:2514px">
    <div class="post-image" role="img" aria-label="Photo of a couple reviewing bills and paperwork at a kitchen table" style="background:linear-gradient(135deg,#e6ddd2,#b59a80 55%,#7c6656)"></div>
    <div class="post-title">SED UT PERSPICIATIS UNDE OMNIS ISTE NATUS ERROR SIT VOLUPTATEM ACCUSANTIUM</div>
    <div class="post-body">At vero eos et accusamus et iusto odio dignissimos ducimus qui blanditiis praesentium voluptatum deleniti atque corrupti quos dolores et quas molestias excepturi sint occaecati</div>
    <div class="post-rule"></div>
    <div class="post-date">FEBRUARY 12 2018</div>
  </article>
  <article class="abs post" style="left:433px;top:2514px">
    <div class="post-image" role="img" aria-label="Photo of a loan officer meeting with clients at an office desk" style="background:linear-gradient(135deg,#eef0f2,#b9bec5 55%,#6f7680)"></div>
    <div class="post-title">UNDE OMNIS ISTE NATUS ERROR SIT VOLUPTATEM ACCUSANTIUM</div>
    <div class="post-body">At vero eos et accusamus et iusto odio dignissimos ducimus qui blanditiis praesentium voluptatum deleniti atque corrupti quos dolores et quas molestias excepturi sint occaecati</div>
    <div class="post-rule"></div>
    <div class="post-date">FEBRUARY 10 2018</div>
  </article>
  <article class="abs post" style="left:796px;top:2514px">
    <div class="post-image" role="img" aria-label="Photo of a smiling couple signing documents with an advisor" style="background:linear-gradient(135deg,#f0ece6,#c3ab93 55%,#8b7867)"></div>
    <div class="post-title">PERSPICIATIS UNDE OMNIS ISTE NATUS ERROR SIT VOLUPTATEM ACCUSANTIUM</div>
    <div class="post-body">At vero eos et accusamus et iusto odio dignissimos ducimus qui blanditiis praesentium voluptatum deleniti atque corrupti quos dolores et quas molestias excepturi sint occaecati</div>
    <div class="post-rule"></div>
    <div class="post-date">FEBRUARY 9 2018</div>
  </article>
  <div class="abs btn-outline blog-more">VIEW MORE BLOG</div>
</section>

<footer class="abs footer">
  <div class="abs footer-brand"><span class="brand-dot"></span><span class="brand-name">THE PELKINS TEAM</span></div>
  <div class="abs footer-partners"><span class="badge" role="img" aria-label="Equal housing lender badge"></span><span class="partner-name">BRIGHTWELL HOME LOANS</span></div>

  <div class="abs fcol" style="left:356px;top:48px">
    <div class="fcol-title">QUICK LINKS</div>
    <ul><li>HOME</li><li>ABOUT US</li><li>MORTGAGE 101</li><li>CONTACT US</li></ul>
  </div>
  <div class="abs fcol" style="left:579px;top:48px">
    <div class="fcol-title">OTHER LINKS</div>
    <ul><li>TERMS OF USE</li><li>PRIVACY POLICY</li><li>HELP</li><li>DISCLAIMER</li></ul>
  </div>
  <div class="abs fcol" style="left:796px;top:48px">
    <div class="fcol-title">RESOURCES</div>
    <div class="res-item"><span class="arrow">›</span><div><div class="res-text">At vero eos et accusamus et iusto odio dignissimos ducimus qui blanditiis praesentium voluptatum</div><div class="res-date">FEBRUARY 12th 2018</div></div></div>
    <div class="res-item"><span class="arrow">›</span><div><div class="res-text">Deleniti atque corrupti quos dolores et quas molestias excepturi sint occaecati</div><div class="res-date">FEBRUARY 8th 2018</div></div></div>
  </div>
  <div class="abs res-nav">‹ ›</div>

  <div class="abs disclaimer-title">DISCLAIMER</div>
  <p class="abs disclaimer">Licensed by the Bureau of Lending Affairs under the Pacific Credit Providers Act. Loans made or arranged pursuant to a Pacific Credit Providers Act License. Equal Housing Lender Brightwell Cannot Accept mortgage applications for properties located in New York via this site.</p>
  <div class="abs footer-rule"></div>
  <div class="abs footer-bottom">© 2018 COMPANY NAME | ALL RIGHTS RESERVED</div>
</footer>

</body>
</html>
```